Graphic designs required for HR consulting Website

We need to items designed to be used on our website and in presentations.
Please view our website for design ideas.
http://www.brightmoor.com.au.42.vexaloft.pw
See attached Powerpoint doc for more info.
InfoGraphic 1
Needs to be turned into an infographic that will be embedded into the Brightmoor HR website.
The fonts should be Helvetica Neue and should have the look and feel of the website.
InfoGraphic 2
Needs to be turned into an infographic that will be embedded into the Brightmoor HR website and used in PPT and WORD proposals.
The fonts should be Helvetica Neue, the look and
feel should be consistent with the first infographic.
A mountain analogy is needed that shows how the sequence of services will come together to take businesses on the journey to becoming great.
2 versions of the same information are shown on the following slides. The first is for ease of visibility, the second is to show the sequence of services on the journey.
Samples of possible design ideas for inspiration are at bottom of ppt.
Consulting
- Helvetica

```html
<!DOCTYPE html>
<html lang="en">
<head>
<meta charset="utf-8">
<title>The Journey to Greatness</title>
<link rel="stylesheet" href="https://fonts.googleapis.com/css2?family=Inter:wght@400;500&family=Lexend:wght@600&display=swap">
<style>
  :root {
    --paper: #f9f6f2;
    --navy-deep: #05314f;
    --navy: #08416a;
    --sky: #2a8fd0;
    --rule: #8a9bb0;
    --white: #ffffff;
  }
  html, body { margin: 0; padding: 0; overflow: hidden; background: var(--paper); }
  .canvas { display: block; width: 1200px; height: 847px; background: var(--paper); }
  .step-num { font-family: "Lexend", sans-serif; font-weight: 600; font-size: 52px; letter-spacing: -0.5px; }
  .tier-num { font-family: "Lexend", sans-serif; font-weight: 600; font-size: 46px; letter-spacing: -0.5px; }
  .dark { fill: var(--navy-deep); }
  .light { fill: var(--sky); }
  .service-title { font-family: "Inter", sans-serif; font-weight: 500; font-size: 16px; letter-spacing: -0.4px; }
  .service-text { font-family: "Inter", sans-serif; font-weight: 400; font-size: 16px; letter-spacing: -0.3px; }
  .tier-label { font-family: "Inter", sans-serif; font-weight: 400; font-size: 27px; fill: var(--white); text-anchor: middle; letter-spacing: -0.3px; }
  .rule { stroke: var(--rule); stroke-width: 1; }
  .divider { stroke: var(--navy-deep); stroke-width: 1; stroke-dasharray: 1.5 2.5; }
</style>
</head>
<body>
<svg class="canvas" viewBox="0 0 1200 847" xmlns="http://www.w3.org/2000/svg" role="img" aria-label="Pyramid of services from foundations to embedding greatness">
  <defs>
    <clipPath id="pyramid-shape">
      <polygon points="728,84 1130,718 326,718"/>
    </clipPath>
  </defs>

  <g class="pyramid" clip-path="url(#pyramid-shape)">
    <rect x="300" y="80" width="860" height="640" fill="var(--sky)"/>
    <rect x="300" y="187" width="860" height="107" fill="var(--navy-deep)"/>
    <rect x="300" y="400" width="860" height="106" fill="var(--navy)"/>
    <rect x="300" y="613" width="860" height="106" fill="var(--navy)"/>
  </g>

  <g class="tier-labels">
    <text class="tier-label" x="728" y="218">The</text>
    <text class="tier-label" x="728" y="252">Embedding</text>
    <text class="tier-label" x="728" y="286">Greatness</text>
    <text class="tier-label" x="728" y="342">Developing</text>
    <text class="tier-label" x="728" y="375">Greatness</text>
    <text class="tier-label" x="728" y="448">Resourcing</text>
    <text class="tier-label" x="728" y="481">Greatness</text>
    <text class="tier-label" x="728" y="569">The Heart of Greatness</text>
    <text class="tier-label" x="728" y="659">The Foundations of Greatness:</text>
    <text class="tier-label" x="728" y="693">Trusted advice and compliance support</text>
  </g>

  <g class="tier-numbers">
    <text class="tier-num dark" x="848" y="257">05</text>
    <text class="tier-num light" x="912" y="363">04</text>
    <text class="tier-num dark" x="978" y="470">03</text>
    <text class="tier-num light" x="1042" y="575">02</text>
    <text class="tier-num dark" x="1110" y="682">01</text>
  </g>

  <g class="step step-05">
    <text class="step-num dark" x="46" y="119">05</text>
    <rect x="122" y="56" width="9" height="96" fill="var(--navy-deep)"/>
    <text class="service-text dark" x="145" y="89">On-site strategic and</text>
    <text class="service-text dark" x="145" y="109">operational support to</text>
    <text class="service-text dark" x="145" y="129">sustain your journey</text>
    <line class="rule" x1="132" y1="140" x2="344" y2="140"/>
  </g>

  <g class="step step-04">
    <text class="step-num light" x="46" y="241">04</text>
    <rect x="122" y="177" width="9" height="97" fill="var(--sky)"/>
    <text class="service-title light" x="142" y="227">Develop Star Players</text>
    <text class="service-text light" x="142" y="247">Leadership coaching</text>
    <line class="divider" x1="312" y1="180" x2="312" y2="252"/>
    <text class="service-title light" x="331" y="210">Create Star Teams</text>
    <text class="service-text light" x="331" y="232">Leadership</text>
    <text class="service-text light" x="331" y="249">development programs</text>
    <line class="rule" x1="132" y1="264" x2="503" y2="264"/>
  </g>

  <g class="step step-03">
    <text class="step-num dark" x="46" y="364">03</text>
    <rect x="122" y="299" width="9" height="97" fill="var(--navy-deep)"/>
    <text class="service-title dark" x="143" y="330">Culture Lens</text>
    <text class="service-text dark" x="143" y="352">Pre-employment</text>
    <text class="service-text dark" x="143" y="369">assessments</text>
    <line class="divider" x1="312" y1="302" x2="312" y2="374"/>
    <text class="service-title dark" x="332" y="330">Hiring Partner</text>
    <text class="service-text dark" x="332" y="352">The expertise to select</text>
    <text class="service-text dark" x="332" y="369">great people</text>
    <line class="rule" x1="132" y1="382" x2="506" y2="382"/>
  </g>

  <g class="step step-02">
    <text class="step-num light" x="46" y="485">02</text>
    <rect x="122" y="420" width="9" height="350" fill="var(--sky)"/>
    <text class="service-title light" x="140" y="457">Step 1: Defining greatness</text>
    <text class="service-text light" x="140" y="479">Business strategy, KPIs,</text>
    <text class="service-text light" x="140" y="497">behaviours and role</text>
    <text class="service-text light" x="140" y="515">clarity</text>
    <line class="rule" x1="132" y1="530" x2="338" y2="530"/>
    <text class="service-title light" x="140" y="563">Step 2:</text>
    <text class="service-title light" x="140" y="583">Measuring Greatness</text>
    <text class="service-text light" x="140" y="604">Creating a culture</text>
    <text class="service-text light" x="140" y="623">of accountability</text>
    <line class="rule" x1="132" y1="638" x2="306" y2="638"/>
    <text class="service-title light" x="140" y="671">Step 3:</text>
    <text class="service-title light" x="140" y="691">Rewarding greatness</text>
    <text class="service-text light" x="140" y="715">Remuneration and</text>
    <text class="service-text light" x="140" y="732">incentive schemes</text>
    <line class="rule" x1="132" y1="746" x2="300" y2="746"/>
  </g>
</svg>
</body>
</html>
```